"Vine Hollow Excursions" is a top notch Santa Barbara County Wine Tour company.

We provide scenic, boutique and custom wine tours. I need the card to be clean and classy. I will provide our logo. I would like the logo to cover the back side of the card as an option and would like to see a couple color options other then our signature green and gold. I would like to see some creative options and let the designers come up with options.
I need cards for myself and my team. The final design should communicate "An authentic and boutique wine tour experience"
Please use my website for reference www.vinehollowexcursions.example

Target Market(s)

We have a wide range of clients from millennials to baby boomers

Industry/Entity Type

Tour

Contact Information for Business Card

Contact info:
Dale Morton
805-219-6384
info@vinehollowexcursions.example
vinehollowexcursions.example

Colors

Designer to choose colors to be used in the design.

Requirements
Must have
• my logo
Nice to have
• *I would like to have the backside side with the logo and the company statement
• "An authentic and boutique wine tour experience" as an option.
• *I would also like to see what the designers can create!
• *I would like to see an option that incorporates or social: instagram, yelp, trip advisor
Should not have
• I do not want it too busy.

```html
<!DOCTYPE html>
<html lang="en">
<head>
<meta charset="utf-8">
<title>Vine Hollow Excursions – Business Card</title>
<link rel="stylesheet" href="https://fonts.googleapis.com/css2?family=Roboto+Condensed:wght@700&family=Roboto:wght@400;500&display=swap">
<style>
  :root {
    --stage: #e9e2d6;
    --vine-green: #236a44;
    --vine-green-light: #3f8a5f;
    --paper: #f7f7f5;
    --white: #ffffff;
    --badge-brown: #8a6a4c;
    --badge-green: #4f9a3a;
    --badge-red: #d8322b;
  }
  * { box-sizing: border-box; margin: 0; padding: 0; }
  html, body { width: 1200px; height: 911px; overflow: hidden; background: var(--stage); }
  .stage {
    position: relative; width: 1200px; height: 911px;
    display: flex; justify-content: center; align-items: center; gap: 80px;
  }
  .card {
    position: relative; width: 380px; height: 665px; overflow: hidden;
    box-shadow: 0 10px 28px rgba(60, 45, 25, 0.25);
  }

  /* Front */
  .card-front { background: var(--vine-green); color: var(--white); }
  .front-brand {
    position: absolute; top: 62px; left: 0; right: 0; text-align: center;
    font-family: "Roboto", sans-serif; font-weight: 500; font-size: 24px; line-height: 1.3;
  }
  .front-brand::after {
    content: ""; display: block; width: 250px; height: 1px; margin: 16px auto 0;
    background: rgba(255,255,255,0.7);
  }
  .holder-name {
    position: absolute; top: 192px; left: 0; right: 0; text-align: center;
    font-family: "Roboto Condensed", sans-serif; font-weight: 700; font-size: 24px; letter-spacing: 0.5px;
  }
  .contact-list {
    position: absolute; top: 246px; left: 0; right: 0; list-style: none;
    font-family: "Roboto", sans-serif; font-weight: 400; font-size: 14.5px; text-align: center;
  }
  .contact-item { display: flex; flex-direction: column; align-items: center; gap: 3px; margin-bottom: 6px; }
  .contact-icon { width: 13px; height: 13px; fill: var(--white); }
  .landscape-area {
    position: absolute; left: 0; right: 0; bottom: 0; height: 255px;
    background: linear-gradient(170deg, var(--white) 0%, #dfeee5 35%, var(--vine-green-light) 100%);
  }

  /* Back */
  .card-back { background: var(--paper); }
  .social-badges { position: absolute; top: 28px; left: 26px; display: flex; gap: 6px; }
  .social-badge { width: 30px; height: 30px; border-radius: 5px; }
  .social-badge.is-photo { background: var(--badge-brown); }
  .social-badge.is-travel { background: var(--badge-green); }
  .social-badge.is-review { background: var(--badge-red); }
  .back-brand {
    position: absolute; top: 250px; left: 0; right: 0; text-align: center;
    display: flex; flex-direction: column; align-items: center; gap: 16px;
  }
  .brand-dot { width: 54px; height: 54px; border-radius: 50%; background: var(--vine-green); }
  .back-brand-name {
    font-family: "Roboto", sans-serif; font-weight: 500; font-size: 26px; line-height: 1.3;
    color: var(--vine-green);
  }
  .statement-band {
    position: absolute; left: 0; right: 0; bottom: 34px; height: 40px;
    background: var(--vine-green); color: var(--white);
    display: flex; align-items: center; justify-content: center;
    font-family: "Roboto", sans-serif; font-weight: 400; font-size: 14.5px; letter-spacing: 0.3px;
  }
</style>
</head>
<body>
<main class="stage">
  <article class="card card-front">
    <p class="front-brand">Vine Hollow<br>Excursions</p>
    <h1 class="holder-name">DALE MORTON</h1>
    <ul class="contact-list">
      <li class="contact-item">
        <svg class="contact-icon" viewBox="0 0 24 24" aria-hidden="true"><path d="M6.6 10.8a15.1 15.1 0 0 0 6.6 6.6l2.2-2.2a1 1 0 0 1 1-.25 11.4 11.4 0 0 0 3.6.57 1 1 0 0 1 1 1V20a1 1 0 0 1-1 1A17 17 0 0 1 3 4a1 1 0 0 1 1-1h3.5a1 1 0 0 1 1 1c0 1.25.2 2.45.57 3.6a1 1 0 0 1-.25 1z"/></svg>
        <span>805-219-6384</span>
      </li>
      <li class="contact-item">
        <svg class="contact-icon" viewBox="0 0 24 24" aria-hidden="true"><path d="M2 5h20v14H2z M2 5l10 8 10-8" stroke="#236a44" stroke-width="1.6"/></svg>
        <span>info@vinehollowexcursions.example</span>
      </li>
      <li class="contact-item">
        <svg class="contact-icon" viewBox="0 0 24 24" aria-hidden="true"><circle cx="12" cy="12" r="10"/></svg>
        <span>vinehollowexcursions.example</span>
      </li>
    </ul>
    <div class="landscape-area" role="img" aria-label="Illustration of vineyard rows beneath a mountain with a rising sun"></div>
  </article>

  <article class="card card-back">
    <div class="social-badges">
      <span class="social-badge is-photo"></span>
      <span class="social-badge is-travel"></span>
      <span class="social-badge is-review"></span>
    </div>
    <div class="back-brand">
      <span class="brand-dot"></span>
      <p class="back-brand-name">Vine Hollow<br>Excursions</p>
    </div>
    <p class="statement-band">An authentic &amp; boutique wine tour experience</p>
  </article>
</main>
</body>
</html>
```